Brightbay Orthodontics business card design

Need a business card design that reflects our re-branding (orthodontic office - braces) and a new partnership with a pediatric dental office. We would like to include "for adults and children" on the card as well so adults know they are welcome to get their braces here as well. Office design is modern and would like business card to reflect a modern type look. Here's the text we would like to be included on the card:

Darren Wolcott, DDS, MSD
5214 West Linden Avenue, Suite 204
Mansfield, TX 76991
555-418-2637
www.brightbayortho.example
info@brightbayortho.example

Can we add the following to the existing designs? Darren Wolcott, DDS, MSD 5214 West Linden Avenue, Suite 204 Mansfield, TX 76991 555-418-2637

Does anyone have any more vertical designs available? Thanks!

Dental

```html
<!DOCTYPE html>
<html lang="en">
<head>
<meta charset="utf-8">
<title>Brightbay Orthodontics – Business Card</title>
<link rel="stylesheet" href="https://fonts.googleapis.com/css2?family=Comic+Neue:wght@400;700&display=swap">
<style>
  :root {
    --page-bg: #e4e4e4;
    --card-bg: #ffffff;
    --band-grey: #6b6c6e;
    --text-grey: #6a6a6a;
    --name-blue: #7b9bc9;
    --accent-green: #8cc63f;
    --accent-blue: #3a66b0;
    --tooth-light: #f4f4f4;
    --tooth-shade: #d6d6d6;
  }
  * { box-sizing: border-box; margin: 0; padding: 0; }
  html, body {
    width: 1200px; height: 753px; overflow: hidden;
    background: var(--page-bg);
    font-family: "Comic Neue", "Comic Sans MS", cursive;
  }
  .stage { position: relative; width: 1200px; height: 753px; }
  .card {
    position: absolute; top: 88px;
    width: 330px; height: 577px;
    background: var(--card-bg);
    overflow: hidden;
    box-shadow: 0 6px 18px rgba(0,0,0,.12);
  }

  /* Appointment side */
  .card--appointment { left: 225px; }
  .appointment-layout {
    position: absolute; left: 0; top: 577px;
    width: 577px; height: 330px;
    transform: rotate(-90deg); transform-origin: 0 0;
    padding: 40px 36px;
  }
  .appointment-brand {
    font-weight: 700; color: var(--text-grey);
    font-size: 40px; line-height: 1.05;
  }
  .appointment-brand .brand-dot {
    display: inline-block; width: 22px; height: 22px;
    background: var(--text-grey); border-radius: 50%;
    margin-right: 12px; vertical-align: middle;
  }
  .appointment-title {
    margin-top: 70px; color: var(--name-blue);
    font-size: 22px; font-weight: 700;
  }
  .appointment-fields {
    display: flex; gap: 18px; margin-top: 14px;
    color: var(--text-grey); font-size: 20px;
  }
  .appointment-field { display: flex; align-items: baseline; flex: 1; }
  .appointment-field .fill-line {
    flex: 1; margin-left: 6px; border-bottom: 2px dotted var(--text-grey);
  }

  /* Contact side */
  .card--contact { left: 645px; }
  .header-band { position: absolute; left: 0; top: 0; width: 330px; height: 190px; }
  .contact-brand {
    position: absolute; left: 0; right: 0; top: 48px;
    text-align: center; color: #fff;
    font-weight: 700; font-size: 30px; line-height: 1.05;
  }
  .tooth-art {
    position: absolute; right: -60px; top: 230px;
    width: 170px; height: 260px; border-radius: 80px 80px 40px 40px;
    background: radial-gradient(circle at 35% 30%, var(--tooth-light), var(--tooth-shade));
  }
  .person { position: absolute; left: 0; width: 250px; top: 228px; text-align: center; }
  .person-name { color: var(--name-blue); font-weight: 700; font-size: 24px; }
  .person-credentials { color: var(--text-grey); font-size: 14px; margin-top: 2px; }
  .contact-details {
    position: absolute; left: 24px; top: 352px;
    color: var(--text-grey); font-size: 15px; line-height: 1.35;
  }
  .contact-address { margin-bottom: 16px; }
  .contact-line { display: flex; align-items: center; gap: 10px; }
  .contact-line svg { width: 13px; height: 13px; flex: none; }
  .footer-stripes { position: absolute; left: 0; bottom: 0; width: 330px; height: 80px; }
</style>
</head>
<body>
<main class="stage">

  <section class="card card--appointment" aria-label="Appointment card side">
    <div class="appointment-layout">
      <div class="appointment-brand"><span class="brand-dot"></span>Brightbay<br>Orthodontics</div>
      <div class="appointment-title">Next Appointment</div>
      <div class="appointment-fields">
        <div class="appointment-field">Date <span class="fill-line"></span></div>
        <div class="appointment-field">Time <span class="fill-line"></span></div>
      </div>
    </div>
  </section>

  <section class="card card--contact" aria-label="Contact card side">
    <svg class="header-band" viewBox="0 0 330 190" aria-hidden="true">
      <polygon points="0,0 330,0 330,110 175,175 0,110" fill="var(--accent-green)"/>
      <polygon points="0,0 330,0 330,104 175,168 0,104" fill="var(--band-grey)"/>
    </svg>
    <div class="contact-brand">Brightbay<br>Orthodontics</div>

    <div class="tooth-art" role="img" aria-label="Soft white tooth illustration"></div>

    <div class="person">
      <div class="person-name">Darren Wolcott</div>
      <div class="person-credentials">DDS, MSD</div>
    </div>

    <div class="contact-details">
      <div class="contact-address">5214 West Linden Avenue, Suite 204<br>Mansfield, TX 76991</div>
      <div class="contact-line">
        <svg viewBox="0 0 16 16" aria-hidden="true"><path d="M3 1h3l1 4-2 1a9 9 0 0 0 5 5l1-2 4 1v3a2 2 0 0 1-2 2A13 13 0 0 1 1 3a2 2 0 0 1 2-2z" fill="var(--name-blue)"/></svg>
        555-418-2637
      </div>
      <div class="contact-line">
        <svg viewBox="0 0 16 16" aria-hidden="true"><circle cx="8" cy="8" r="6.5" fill="none" stroke="var(--name-blue)" stroke-width="1.5"/><path d="M1.5 8h13M8 1.5c-3 3.5-3 9.5 0 13M8 1.5c3 3.5 3 9.5 0 13" fill="none" stroke="var(--name-blue)" stroke-width="1.2"/></svg>
        www.brightbayortho.example
      </div>
      <div class="contact-line">
        <svg viewBox="0 0 16 16" aria-hidden="true"><rect x="1" y="3" width="14" height="10" fill="var(--name-blue)"/><path d="M1 3l7 6 7-6" fill="none" stroke="#fff" stroke-width="1.3"/></svg>
        info@brightbayortho.example
      </div>
    </div>

    <svg class="footer-stripes" viewBox="0 0 330 80" aria-hidden="true">
      <polygon points="0,62 330,0 330,12 0,74" fill="var(--accent-green)"/>
      <polygon points="0,68 250,20 250,80 0,80" fill="var(--accent-blue)"/>
    </svg>
  </section>

</main>
</body>
</html>
```